Fitness Equipment & Service

I want to make the card eye catching and fun. We are called Corvane Motion Limited and we are based in Wales. We sell, install and service all types of fitness equipment from Skipping ropes, right through the Dumbbells, Kettle bells and Barbells through to state of the art Treadmills, Running Machines and Strength Equipment. We also design and install changing room furniture and lockers.

TYPOGRAPHY
We would like to use Futrura. Futura has an appearance of efficiency and forwardness. The typeface is derived
from simple geometric forms (near-perfect circles, triangles and squares) and is based on strokes of
near-even weight, which are low in contrast. This is most visible in the almost perfectly round stroke of
the o, which is nonetheless slightly ovoid.
The lowercase has tall ascenders, which rise above the cap line. The uppercase
characters present proportions similar to those of classical Roman capitals.

TYPOGRAPHIC CONSIDERATIONS
No Strike though
No Horizontal Scaling
No Drop Shadows
No Effects
Never use less than 120% Leading

OUR CORPORATE COLOURS
BRAND GUIDELINES
We were thinking that our primary colour palette consists of the Acid Green (Pantone 382) and Process Black.

We work closely with tquarly Ltd and would like to include their name on the card somewhere. I have attached images of the other brands that we work with as an idea or the small icons I have included that illustrate what we do?. I have very kindly been given permission to use any of the images off the files that I have included below, so I hope these help. I will include these below. I would be open to suggestions if it made the card more striking Can you do it?
Updates

Hi All, Just wanted to add a few thoughts but you are the guys with the creative visions (thats why are here) We are based in Wales, UK and we would be open to lots of different ideas on a theme but must be eye catching, Bold and FUN. If you can or think that the Welsh or any dragon could be put in there then go for it (its not a must have) We have also added some ideas for colour but again its over to you!! GO FOR IT ! Thanks and look forward to your visions! Owen

Hi All, Just thought I would sen through the contact details that need to be on the card. (if you want to play around with icons instead of the wording twitter, Facebook, go for it): Corvane Motion Limited Owen Pritchard Managing Director Mob: +44 (0)7582 913 406 e-mail: sales@corvanemotion.co.uk Web: Corvanemotion.co.uk twitter: @motionLetterbin Facebook: Corvane Motion Limited

```html
<!DOCTYPE html>
<html lang="en">
<head>
<meta charset="utf-8">
<title>Corvane Motion Limited – Business Card</title>
<link rel="stylesheet" href="https://fonts.googleapis.com/css2?family=Open+Sans:wght@400;700&display=swap">
<style>
  :root {
    --canvas-bg: #e8e5e0;
    --card-white: #f7f7f8;
    --card-black: #0b0b0c;
    --gold: #e3b53b;
    --navy: #242a6b;
    --globe-blue: #2f4fb0;
    --text-light: #f2f2f2;
    --social-blue: #3f6fc4;
  }
  * { margin: 0; padding: 0; box-sizing: border-box; }
  html, body {
    width: 1200px;
    height: 892px;
    overflow: hidden;
  }
  body {
    background: var(--canvas-bg);
    font-family: "Open Sans", sans-serif;
    display: flex;
    align-items: center;
    justify-content: center;
    gap: 80px;
  }
  .card {
    width: 350px;
    height: 600px;
    border-radius: 4px;
    position: relative;
    box-shadow: 0 8px 24px rgba(0,0,0,0.18);
  }

  /* Front */
  .card--front {
    background: var(--card-white);
    display: flex;
    flex-direction: column;
    align-items: center;
    justify-content: center;
    gap: 34px;
  }
  .brand-mark {
    width: 170px;
    height: 170px;
    border-radius: 50%;
    background: radial-gradient(circle at 40% 35%, #4b6fd0, var(--globe-blue) 60%, #1c2f80);
    border: 5px solid #d9dbe2;
  }
  .brand-name {
    color: var(--navy);
    font-weight: 700;
    font-size: 22px;
    line-height: 1.3;
    letter-spacing: 1px;
    text-transform: uppercase;
    text-align: center;
  }

  /* Back */
  .card--back {
    background: var(--card-black);
    color: var(--text-light);
    padding: 44px 34px 0 34px;
  }
  .contact {
    text-align: right;
  }
  .contact__name {
    color: var(--gold);
    font-weight: 700;
    font-size: 30px;
    line-height: 1.2;
  }
  .contact__title {
    font-size: 19px;
    line-height: 1.3;
    margin-bottom: 34px;
  }
  .contact__line {
    display: flex;
    justify-content: flex-end;
    align-items: center;
    gap: 12px;
    font-size: 15.5px;
    line-height: 1.9;
  }
  .contact__icon {
    width: 16px;
    height: 16px;
    flex: none;
  }
  .social {
    margin-top: 34px;
  }
  .social .contact__line { font-size: 16px; line-height: 2.1; }
  .social__square {
    width: 24px;
    height: 24px;
    border-radius: 3px;
    background: var(--social-blue);
    flex: none;
  }
  .back-brand {
    position: absolute;
    left: 0; right: 0;
    bottom: 46px;
    display: flex;
    flex-direction: column;
    align-items: center;
    gap: 22px;
  }
  .back-brand .brand-mark {
    width: 150px;
    height: 150px;
    border-color: #e9e9ee;
  }
  .back-brand .brand-name {
    color: var(--text-light);
    font-weight: 400;
    font-size: 18px;
  }
</style>
</head>
<body>

  <section class="card card--front" aria-label="Card front">
    <div class="brand-mark"></div>
    <p class="brand-name">Corvane Motion<br>Limited</p>
  </section>

  <section class="card card--back" aria-label="Card back">
    <div class="contact">
      <p class="contact__name">Owen Pritchard</p>
      <p class="contact__title">Managing Director</p>

      <p class="contact__line">+44 (0)7582 913 406
        <svg class="contact__icon" viewBox="0 0 16 16" aria-hidden="true">
          <rect width="16" height="16" rx="2" fill="var(--gold)"/>
          <rect x="5" y="3" width="6" height="10" rx="1" fill="none" stroke="#111" stroke-width="1.4"/>
          <circle cx="8" cy="11" r="0.8" fill="#111"/>
        </svg>
      </p>
      <p class="contact__line">sales@corvanemotion.co.uk
        <svg class="contact__icon" viewBox="0 0 16 16" aria-hidden="true">
          <rect width="16" height="16" rx="2" fill="var(--gold)"/>
          <rect x="3" y="4.5" width="10" height="7" fill="none" stroke="#111" stroke-width="1.3"/>
          <path d="M3 4.5 L8 9 L13 4.5" fill="none" stroke="#111" stroke-width="1.3"/>
        </svg>
      </p>
      <p class="contact__line">Corvanemotion.co.uk
        <svg class="contact__icon" viewBox="0 0 16 16" aria-hidden="true">
          <rect width="16" height="16" rx="2" fill="var(--gold)"/>
          <circle cx="8" cy="8" r="4.5" fill="none" stroke="#111" stroke-width="1.3"/>
          <path d="M3.5 8 H12.5 M8 3.5 C5.5 6 5.5 10 8 12.5 M8 3.5 C10.5 6 10.5 10 8 12.5" fill="none" stroke="#111" stroke-width="1"/>
        </svg>
      </p>

      <div class="social">
        <p class="contact__line">@motionLetterbin <span class="social__square"></span></p>
        <p class="contact__line">Corvane Motion Limited <span class="social__square"></span></p>
      </div>
    </div>

    <div class="back-brand">
      <div class="brand-mark"></div>
      <p class="brand-name">Corvane Motion<br>Limited</p>
    </div>
  </section>

</body>
</html>
```